Request for Business Card Design

Hi. My name is Marlene, I am looking for a new business card design for my company, Quarrow Signal Instruments, LLC. I really like the design you did for Tarsel Venture and was hoping you could do something similar using our full logo and our mark. I am also open to any raised texture design using our mark. I have attached our full logo, which would need to be somewhere on the card, as well as the mark in both outline and full form, as well as our brand colors / guide. The card does not have to be white, as long as our logo and mark appear. I actually like darker colored business cards more, but am open to all options. If you are interested in working with me, please let me know. We would also take the business card design into letterhead design if you can do that.

```html
<!DOCTYPE html>
<html lang="en">
<head>
<meta charset="utf-8">
<title>Quarrow Signal Instruments – Business Card</title>
<link href="https://fonts.googleapis.com/css2?family=Roboto:wght@400;500;700&display=swap" rel="stylesheet">
<style>
  :root {
    --backdrop: #2a2a2a;
    --card: #1d1d1e;
    --accent: #0a9ac8;
    --text: #ffffff;
    --muted: #d9d9d9;
    --rule: #1f3a7a;
    --stripe: #cfcfcf;
  }
  * { margin: 0; padding: 0; box-sizing: border-box; }
  html, body { width: 1200px; height: 866px; overflow: hidden; }
  body {
    background: var(--backdrop);
    font-family: "Roboto", Arial, sans-serif;
    color: var(--text);
    position: relative;
  }
  .card {
    position: absolute;
    top: 278px;
    width: 540px;
    height: 310px;
    background: var(--card);
    overflow: hidden;
    box-shadow: 0 12px 30px rgba(0,0,0,.45);
  }
  .card--front { left: 40px; }
  .card--back { left: 620px; }

  .brand {
    position: absolute;
    display: flex;
    align-items: center;
    gap: 12px;
  }
  .brand__dot {
    flex: none;
    border-radius: 50%;
    background: var(--accent);
  }
  .brand__name {
    font-weight: 700;
    text-transform: uppercase;
    letter-spacing: .08em;
    color: var(--text);
    line-height: 1.1;
  }
  .card--front .brand { left: 70px; top: 120px; }
  .card--front .brand__dot { width: 52px; height: 52px; }
  .card--front .brand__name { font-size: 27px; width: 330px; }

  .card--back .brand { left: 300px; top: 86px; }
  .card--back .brand__dot { width: 34px; height: 34px; }
  .card--back .brand__name { font-size: 16px; width: 190px; }

  .person { position: absolute; left: 28px; top: 36px; }
  .person__name {
    font-size: 19px; font-weight: 500; letter-spacing: .04em;
    color: var(--accent); text-transform: uppercase;
  }
  .person__role { font-size: 15px; color: var(--text); margin-top: 2px; }
  .contact { margin-top: 10px; font-size: 14px; line-height: 1.45; letter-spacing: .03em; }
  .contact__row { display: flex; align-items: center; gap: 7px; }
  .contact__icon { width: 13px; height: 13px; flex: none; }

  .divider {
    position: absolute; left: 28px; top: 150px;
    width: 480px; height: 1px; background: var(--rule);
  }
  .address {
    position: absolute; right: 34px; top: 178px;
    text-align: right; font-size: 14px; line-height: 1.35; letter-spacing: .03em;
  }
  .footer-band { position: absolute; left: 0; bottom: 0; width: 540px; height: 80px; }
  .website {
    position: absolute; right: 34px; bottom: 12px;
    font-size: 15px; font-weight: 500; letter-spacing: .05em; color: var(--text);
  }
</style>
</head>
<body>

  <section class="card card--front" aria-label="Card front">
    <div class="brand">
      <span class="brand__dot"></span>
      <span class="brand__name">Quarrow Signal Instruments</span>
    </div>
  </section>

  <section class="card card--back" aria-label="Card back">
    <div class="person">
      <p class="person__name">Daniel Hartley</p>
      <p class="person__role">Managing Director</p>
      <div class="contact">
        <p class="contact__row">
          <svg class="contact__icon" viewBox="0 0 16 16" aria-hidden="true"><path fill="#0a9ac8" d="M3.6 1.2l2.3 2.6-1.2 1.9c.9 2 2.5 3.6 4.5 4.5l1.9-1.2 2.6 2.3-1.3 2.3C7 13.3 2.7 9 1.3 2.5z"/></svg>
          044-210 987 654
        </p>
        <p class="contact__row">
          <svg class="contact__icon" viewBox="0 0 16 16" aria-hidden="true"><rect x="1" y="3" width="14" height="10" fill="#0a9ac8"/><path d="M1 3l7 6 7-6" fill="none" stroke="#1d1d1e" stroke-width="1.4"/></svg>
          info@quarrowsignal.com
        </p>
      </div>
    </div>

    <div class="brand">
      <span class="brand__dot"></span>
      <span class="brand__name">Quarrow Signal Instruments</span>
    </div>

    <div class="divider"></div>

    <p class="address">88, Harbor Lane Suite 4<br>30215, Fenwick</p>

    <svg class="footer-band" viewBox="0 0 540 80" aria-hidden="true">
      <path d="M0 34 L200 66 L0 66 Z" fill="var(--stripe)"/>
      <path d="M0 40 L180 68 C190 60 205 52 230 52 C255 52 270 58 290 80 L0 80 Z" fill="var(--accent)"/>
      <path d="M200 80 C230 44 260 44 290 46 L540 46 L540 80 Z" fill="var(--accent)"/>
    </svg>
    <p class="website">www.quarrowsignal.com</p>
  </section>

</body>
</html>
```